Aerial Imaging and photgraphy business card

Design a business card with eye catching aerial photo of country side / landscape with a drone in the foreground.
Also contact details.

Target Market(s)

Aerial Imaging photography

Industry/Entity Type

Advertising

Contact Information for Business Card

Rowland
0412965203
Website http://www.skywardvistaphoto.com.au/
email address : skywardvistaphoto.com.au

Colors
e8f1ca
cadf82
9bcb3c
33a6d7
85cae6
cee9f5

Requirements
Must have
• High res photo
• Korvane drone in the foreground Either T4200 and korvane Glidewing or both
Nice to have
• high resolution landscape country photo on the front of the card with a Korvane T4200 drone in the foreground.

```html
<!DOCTYPE html>
<html lang="en">
<head>
<meta charset="utf-8">
<title>Skyward Vista Photo – Business Card</title>
<link href="https://fonts.googleapis.com/css2?family=Open+Sans:wght@400;600&display=swap" rel="stylesheet">
<style>
  :root {
    --page-bg: #e4e6e8;
    --card-bg: #f7f7f7;
    --panel-top: #6a9fc0;
    --panel-bottom: #7bbde2;
    --band: #f4f4f4;
    --ink-dark: #2f2f2f;
    --ink-name: #4b6a84;
    --ink-white: #ffffff;
    --brand: #3d4a55;
    --sky-top: #85cae6;
    --sky-low: #cee9f5;
    --field-light: #9bcb3c;
    --field-deep: #4f8f2a;
  }
  * { margin: 0; padding: 0; box-sizing: border-box; }
  html, body {
    width: 1200px; height: 900px; overflow: hidden;
    background: var(--page-bg);
    font-family: "Open Sans", Arial, sans-serif;
  }
  .card {
    position: absolute; left: 150px; top: 180px;
    width: 900px; height: 540px;
    background: var(--card-bg);
    border-radius: 26px;
    overflow: hidden;
    box-shadow: 0 10px 30px rgba(0,0,0,0.15);
  }
  .card__shapes { position: absolute; inset: 0; }
  .card__website {
    position: absolute; left: 30px; top: 190px; width: 430px;
    font-size: 22px; color: var(--ink-dark);
    transform: rotate(6deg); transform-origin: left center;
    white-space: nowrap;
  }
  .card__contact {
    position: absolute; left: 30px; width: 380px; top: 345px;
    text-align: center; color: var(--ink-white);
    font-size: 24px; line-height: 37px;
  }
  .aerial-photo {
    position: absolute; left: 545px; top: 48px;
    width: 290px; height: 220px;
    border-radius: 30px;
    background: linear-gradient(180deg,
      var(--sky-top) 0%, var(--sky-low) 42%,
      var(--field-light) 58%, var(--field-deep) 100%);
  }
  .brand {
    position: absolute; left: 505px; top: 286px; width: 370px;
    text-align: center;
  }
  .brand__name {
    font-size: 31px; font-weight: 600; line-height: 40px;
    color: var(--brand); white-space: nowrap;
  }
  .person {
    position: absolute; right: 75px; top: 432px; text-align: right;
  }
  .person__name { font-size: 30px; font-weight: 600; color: var(--ink-name); line-height: 40px; }
  .person__role { font-size: 23px; color: var(--ink-dark); line-height: 32px; }
</style>
</head>
<body>
  <div class="card">
    <svg class="card__shapes" width="900" height="540" viewBox="0 0 900 540">
      <defs>
        <linearGradient id="panelFill" x1="0" y1="0" x2="0" y2="1">
          <stop offset="0" stop-color="var(--panel-top)"/>
          <stop offset="1" stop-color="var(--panel-bottom)"/>
        </linearGradient>
      </defs>
      <polygon class="card__panel" fill="url(#panelFill)"
        points="0,55 42,0 263,0 485,110 485,420 277,540 125,540 0,505"/>
      <path class="card__band" fill="var(--band)"
        d="M0,165 Q152,95 485,192 L485,293 Q250,205 0,259 Z"/>
    </svg>

    <div class="card__website">www.skywardvistaphoto.com.au</div>

    <div class="card__contact">
      <div>0412 965 203</div>
      <div>info@skywardvistaphoto.com.au</div>
    </div>

    <div class="aerial-photo" role="img"
      aria-label="Aerial photo of green countryside fields with a camera drone in the foreground"></div>

    <div class="brand">
      <div class="brand__name">Skyward Vista Photo</div>
    </div>

    <div class="person">
      <div class="person__name">Rowland Hale</div>
      <div class="person__role">Managing Director</div>
    </div>
  </div>
</body>
</html>
```